New Business Card Options

we need a new business card design to reflect the edgy, innovative image we want the company to portray. We also need to include the social buttons to encourage more interaction with our social media accounts.
I've attached the current business card design which is a fold out card which has lines for writing notes on the back. I'm looking for options for design as well as printing suggestions - we want to stand out and be memorable.
THE BUSINESS CARD DOES NOT HAVE TO HAVE THE PHOTO
Colours to use:
MARINE
Dark blue R000 G031 B051
Light blue R080 G177 B234
Dark blue C100 M047 Y023 K079
Light blue C083 M001 Y000 K000
Updates
Reason: I just need an extra day to shortlist designs
Reason: need more time to decide
Target Market(s)
Marine
Industry/Entity Type
Business
Contact Information for Business Card
I've attached a copy of our current business card. the new business cards may or may not include the photo - i would like options of both. I would like our social media icons adding for Chirply, Workloop, Pagebrook and ReelDeck
Font styles to use
Other font styles liked:
- Calibri
Look and feel
Each slider illustrates characteristics of the customer's brand and the style your logo design should communicate.

```html
<!DOCTYPE html>
<html lang="en">
<head>
<meta charset="utf-8">
<title>Keelwise Marine – Business Card</title>
<link rel="stylesheet" href="https://fonts.googleapis.com/css2?family=Ubuntu:wght@300;400;500;700&display=swap">
<style>
  :root {
    --marine-dark: #001f33;
    --marine-navy: #0d3f8c;
    --marine-light: #50b1ea;
    --sky-pale: #eaf6fd;
    --sky-mid: #8fd0f5;
    --text-grey: #4a5560;
    --icon-grey: #8a9097;
    --icon-blue: #1fa3e6;
    --icon-green: #5cb531;
    --icon-orange: #f6a823;
    --portrait-tone: #c3c9cf;
    --page-bg: #e7e8ea;
  }
  * { box-sizing: border-box; margin: 0; padding: 0; }
  html, body {
    width: 1118px; height: 1200px; overflow: hidden;
    background: var(--page-bg);
    font-family: "Ubuntu", sans-serif;
  }
  .card {
    position: absolute; left: 119px;
    width: 880px; height: 530px;
    border-radius: 40px; overflow: hidden;
    box-shadow: 0 6px 18px rgba(0,0,0,.12);
    background: linear-gradient(100deg, #ffffff 0%, var(--sky-pale) 30%, var(--sky-mid) 74%, var(--marine-light) 100%);
  }
  .card--contact { top: 45px; }
  .card--profile { top: 625px; }

  /* Contact side */
  .brand { position: absolute; left: 70px; top: 222px; width: 270px; }
  .brand__name {
    font-size: 34px; font-weight: 700; color: var(--marine-dark);
    line-height: 1.1; white-space: nowrap;
  }
  .brand__tagline {
    margin-top: 8px; font-size: 17px; font-weight: 500;
    color: var(--marine-light); white-space: nowrap;
  }

  .contact-panel {
    position: absolute; left: 355px; top: 90px;
    width: 470px; height: 232px;
    background: linear-gradient(90deg, rgba(255,255,255,.6), rgba(255,255,255,0));
  }
  .contact-list { list-style: none; }
  .contact-list li { display: flex; align-items: center; height: 58px; }
  .contact-icon {
    flex: none; width: 58px; height: 58px;
    display: flex; align-items: center; justify-content: center;
  }
  .contact-icon--phone { background: var(--icon-grey); }
  .contact-icon--chat { background: var(--icon-blue); }
  .contact-icon--mail { background: var(--icon-green); }
  .contact-icon--web { background: var(--icon-orange); }
  .contact-text { padding-left: 24px; font-size: 17px; font-weight: 300; color: var(--text-grey); }

  .address {
    position: absolute; left: 60px; right: 40px; bottom: 45px;
    display: flex; justify-content: space-between;
    list-style: none; font-size: 16px; color: var(--marine-dark);
  }
  .address li::before { content: "•"; margin-right: 4px; }

  /* Profile side */
  .services {
    position: absolute; left: 40px; top: 78px;
    display: flex; gap: 26px; list-style: none;
    font-size: 20px; color: var(--marine-light);
  }
  .services li::before { content: "•"; color: var(--marine-dark); margin-right: 6px; }
  .portrait {
    position: absolute; left: 120px; top: 130px;
    width: 380px; height: 400px;
    background: radial-gradient(ellipse 60% 70% at 50% 45%, var(--portrait-tone) 0%, #d6dbe0 55%, rgba(234,246,253,0) 100%);
  }
  .social {
    position: absolute; right: 60px; top: 28px;
    display: flex; align-items: center; gap: 8px;
    font-size: 13px; line-height: 1.1; color: #ffffff;
  }
  .social__mark { width: 26px; height: 26px; background: var(--marine-dark); }
  .person { position: absolute; right: 70px; top: 255px; }
  .person__name { font-size: 40px; font-weight: 700; color: var(--marine-navy); }
  .person__role { font-size: 30px; font-weight: 300; color: var(--marine-navy); margin-top: 4px; }
</style>
</head>
<body>

<section class="card card--contact">
  <div class="brand">
    <div class="brand__name">Keelwise Marine</div>
    <div class="brand__tagline">Smarter Routes at Sea</div>
  </div>

  <div class="contact-panel">
    <ul class="contact-list">
      <li>
        <span class="contact-icon contact-icon--phone">
          <svg width="26" height="30" viewBox="0 0 26 30" fill="none" stroke="#fff" stroke-width="2">
            <rect x="6" y="2" width="14" height="26" rx="2"/><line x1="11" y1="24" x2="15" y2="24"/>
          </svg>
        </span>
        <span class="contact-text">+44 (0) 7700 900412</span>
      </li>
      <li>
        <span class="contact-icon contact-icon--chat">
          <svg width="24" height="24" viewBox="0 0 24 24"><rect x="3" y="3" width="18" height="18" rx="3" fill="#fff"/></svg>
        </span>
        <span class="contact-text">sam.harlow12</span>
      </li>
      <li>
        <span class="contact-icon contact-icon--mail">
          <svg width="30" height="22" viewBox="0 0 30 22" fill="none" stroke="#fff" stroke-width="2">
            <rect x="2" y="2" width="26" height="18"/><polyline points="2,2 15,12 28,2"/>
          </svg>
        </span>
        <span class="contact-text">sam.harlow@keelwise-marine.com</span>
      </li>
      <li>
        <span class="contact-icon contact-icon--web">
          <svg width="28" height="28" viewBox="0 0 28 28" fill="none" stroke="#fff" stroke-width="2">
            <circle cx="14" cy="14" r="11"/><ellipse cx="14" cy="14" rx="5" ry="11"/><line x1="3" y1="14" x2="25" y2="14"/>
          </svg>
        </span>
        <span class="contact-text">www.keelwise-marine.com</span>
      </li>
    </ul>
  </div>

  <ul class="address">
    <li>Brindle Park</li><li>Oakmere</li><li>Halston</li><li>West Fenshire</li><li>HF4 2QT</li><li>UK</li>
  </ul>
</section>

<section class="card card--profile">
  <ul class="services">
    <li>Environmental</li><li>Medical</li><li>Navigation</li><li>Safety</li>
  </ul>
  <div class="portrait" role="img" aria-label="Black and white portrait photo of the regional manager"></div>
  <div class="social">
    <span class="social__mark"></span>
    <span>Find me on<br>Workloop</span>
  </div>
  <div class="person">
    <div class="person__name">Sam Harlow</div>
    <div class="person__role">Regional Manager</div>
  </div>
</section>

</body>
</html>
```